4th Generation Family Business Needs a New Card Design!

We are a family owned 4th Generation company. We are based in the Sydney, Australia area and we are desperately in need of a more modern and classy card. We are monumental masons who design, supply & erect lasting memorials throughout cemeteries in Sydney. Our customers are normally in a period of grieving. I have attached logo files that will need to be implemented on the card. Company was established 1935. Australian Owned and Operated. Card needs to be designed to PIXO.com specification.

Target Market(s)

Our target market is based upon people that a grieving for family members that have passed away. We also deal with alot of companies that own and operate cemeteries.

Industry/Entity Type

Business

Contact Information for Business Card

Simon Harcourt, Operations Manager, 0417293086, simon@harcourtmemorials.com.au
Lewis Harcourt, Director, 0491630572, lewis@harcourtmemorials.com.au
Phone # 02 9561 3048
Website: www.harcourtmemorials.com.au
Address: Suite 17, 8 Palfrey Lane, West Carlow, Sydney NSW 2156

Font styles to use
Serif
Decorative
Script

Requirements
Must have
• Would like to see the logo nicely implemented with a modern design. Embossed lettering would be a nice additive.

```html
<!DOCTYPE html>
<html lang="en">
<head>
<meta charset="utf-8">
<title>Harcourt Memorials – Business Card</title>
<link href="https://fonts.googleapis.com/css2?family=Arimo:wght@400;700&display=swap" rel="stylesheet">
<style>
  :root {
    --gold: #e1b52b;
    --gold-dark: #c99d1c;
    --ink: #1d1d1d;
    --grey-top: #a9a9a9;
    --grey-mid: #e6e6e6;
    --paper: #f7f7f7;
    --backdrop: #d9d6d0;
  }
  * { box-sizing: border-box; margin: 0; padding: 0; }
  html, body { width: 1200px; height: 892px; overflow: hidden; }
  body {
    background: var(--backdrop);
    font-family: "Arimo", Arial, sans-serif;
    color: var(--ink);
    display: flex;
    flex-direction: column;
    align-items: center;
    justify-content: center;
    gap: 36px;
  }
  .card {
    width: 660px;
    height: 400px;
    border-radius: 24px;
    overflow: hidden;
    position: relative;
    box-shadow: 0 6px 18px rgba(0,0,0,.18);
  }
  /* Front */
  .card--front {
    background: linear-gradient(to bottom, var(--grey-top) 0%, var(--grey-mid) 45%, var(--paper) 100%);
  }
  .brand {
    position: absolute;
    left: 40px; top: 95px;
    width: 260px;
    display: flex;
    flex-direction: column;
    align-items: center;
    gap: 6px;
  }
  .brand__mark {
    width: 22px; height: 22px;
    background: var(--gold);
    margin-bottom: 10px;
  }
  .brand__name {
    font-weight: 700;
    font-size: 34px;
    letter-spacing: 2px;
    color: var(--ink);
    text-transform: uppercase;
    line-height: 1.1;
    text-align: center;
  }
  .divider {
    position: absolute;
    left: 325px; top: 40px;
    width: 2px; height: 250px;
    background: var(--gold);
  }
  .people {
    position: absolute;
    left: 350px; top: 68px;
    display: flex;
    align-items: flex-start;
    gap: 10px;
  }
  .person__name { font-size: 19px; color: var(--ink); white-space: nowrap; }
  .person__title { font-size: 12.5px; color: var(--gold); margin-top: 1px; }
  .people__bar { width: 2px; height: 34px; background: var(--ink); margin-top: 2px; }
  .contacts {
    position: absolute;
    left: 350px; top: 150px;
    list-style: none;
    display: flex;
    flex-direction: column;
    gap: 8px;
  }
  .contact { display: flex; align-items: flex-start; gap: 14px; font-size: 15px; line-height: 1.15; }
  .contact__icon {
    flex: none;
    width: 20px; height: 18px;
    border-radius: 4px;
    background: var(--gold);
    display: flex; align-items: center; justify-content: center;
  }
  .contact__icon svg { width: 12px; height: 12px; }
  .address-band {
    position: absolute;
    left: 0; right: 0; bottom: 0;
    height: 82px;
    background: linear-gradient(to bottom, var(--gold-dark), var(--gold));
    display: flex; align-items: center; justify-content: center;
    color: #fff;
    font-size: 17px;
    letter-spacing: .3px;
  }
  /* Back */
  .card--back {
    background: linear-gradient(135deg, #fbfbfb, #e9e9e9);
    display: flex; align-items: center; justify-content: center;
  }
  .card--back .brand { position: static; width: auto; }
  .card--back .brand__name { font-size: 46px; }
</style>
</head>
<body>

<section class="card card--front" aria-label="Business card front">
  <div class="brand">
    <div class="brand__mark"></div>
    <div class="brand__name">Harcourt<br>Memorials</div>
  </div>

  <div class="divider"></div>

  <div class="people">
    <div class="person">
      <div class="person__name">Simon Harcourt</div>
      <div class="person__title">Operations Manager</div>
    </div>
    <div class="people__bar"></div>
    <div class="person">
      <div class="person__name">Lewis Harcourt</div>
      <div class="person__title">Director</div>
    </div>
  </div>

  <ul class="contacts">
    <li class="contact">
      <span class="contact__icon"><svg viewBox="0 0 12 12"><rect x="3" y="0.5" width="6" height="11" rx="1" fill="none" stroke="#222" stroke-width="1.2"/><circle cx="6" cy="9.5" r=".7" fill="#222"/></svg></span>
      <span>0417293086 / 0491630572</span>
    </li>
    <li class="contact">
      <span class="contact__icon"><svg viewBox="0 0 12 12"><path d="M2.5 1 L4.5 1 L5.2 3.5 L4 4.5 Q5 7 7.5 8 L8.5 6.8 L11 7.5 L11 9.5 Q10.5 11 9 11 Q2 10 1 3 Q1 1.5 2.5 1Z" fill="#222"/></svg></span>
      <span>02 9561 3048</span>
    </li>
    <li class="contact">
      <span class="contact__icon"><svg viewBox="0 0 12 12"><rect x="1" y="2.5" width="10" height="7" fill="none" stroke="#222" stroke-width="1.1"/><path d="M1 2.5 L6 6.5 L11 2.5" fill="none" stroke="#222" stroke-width="1.1"/></svg></span>
      <span>simon@harcourtmemorials.com.au<br>lewis@harcourtmemorials.com.au</span>
    </li>
    <li class="contact">
      <span class="contact__icon"><svg viewBox="0 0 12 12"><circle cx="6" cy="6" r="5" fill="none" stroke="#222" stroke-width="1"/><ellipse cx="6" cy="6" rx="2.2" ry="5" fill="none" stroke="#222" stroke-width=".9"/><path d="M1 6 H11" stroke="#222" stroke-width=".9"/></svg></span>
      <span>www.harcourtmemorials.com.au</span>
    </li>
  </ul>

  <div class="address-band">Suite 17, 8 Palfrey Lane, West Carlow, Sydney NSW 2156</div>
</section>

<section class="card card--back" aria-label="Business card back">
  <div class="brand">
    <div class="brand__mark"></div>
    <div class="brand__name">Harcourt<br>Memorials</div>
  </div>
</section>

</body>
</html>
```